Stylish new business card needed!

Hello everyone! I am in need of a new business card design for an alarm company here in Hurricane WV. I have all fonts, color codes and logos provided for you use! We are a young company and like the style of a clean sleek looking business card. Would like it double sided, one side holding the logo and the other with your design!
Target Market(s)
The people that are looking for the newest tech for home automation and security
Industry/Entity Type
Alarm services; Home automation
Contact Information for Business Card
Name of person; position (Sales; Installer); Phone Number (555.418.7260); Employee cell Number; Website (www.GuardedByVelk.example); Employee Email; Double sided
Look and feel
Each slider illustrates characteristics of the customer's brand and the style your logo design should communicate.

```html
<!DOCTYPE html>
<html lang="en">
<head>
<meta charset="utf-8">
<title>Velk Business Card</title>
<link rel="stylesheet" href="https://fonts.googleapis.com/css2?family=Montserrat:wght@700;800&family=Open+Sans:wght@400;600&display=swap">
<style>
  :root {
    --stage: #232323;
    --card: #222124;
    --card-deep: #1b1a1d;
    --orange: #f28b45;
    --grey: #9a9a9a;
    --white: #ffffff;
    --ghost: #2b2a2e;
  }
  * { box-sizing: border-box; margin: 0; padding: 0; }
  html, body { width: 1200px; height: 780px; overflow: hidden; }
  body {
    background: var(--stage);
    font-family: "Open Sans", Arial, sans-serif;
    position: relative;
  }
  .card {
    position: absolute;
    top: 235px;
    width: 540px;
    height: 310px;
    border-radius: 18px;
    background: var(--card);
    box-shadow: 0 4px 0 var(--orange), 0 14px 30px rgba(0,0,0,.55);
    overflow: hidden;
  }
  .card--back { left: 45px; }
  .card--front { left: 615px; }

  /* back */
  .back-pattern {
    position: absolute; inset: 0;
    background: linear-gradient(160deg, #2a292d 0%, var(--card) 45%, var(--card-deep) 100%);
  }
  .back-mark {
    position: absolute; right: 78px; top: 118px;
    font-family: "Montserrat", sans-serif; font-weight: 800;
    font-size: 30px; color: var(--grey); letter-spacing: 1px;
  }

  /* front */
  .accent-bar {
    position: absolute; right: 0; top: 0;
    width: 16px; height: 70px; background: var(--orange);
  }
  .person {
    position: absolute; right: 34px; top: 22px; text-align: right;
  }
  .person__name {
    font-family: "Montserrat", sans-serif; font-weight: 800; font-size: 24px;
    line-height: 1.1;
  }
  .person__first { color: var(--orange); }
  .person__last { color: var(--grey); }
  .person__role {
    font-family: "Montserrat", sans-serif; font-weight: 700;
    font-size: 13px; color: var(--white); margin-top: 2px;
  }
  .brand {
    position: absolute; left: 40px; top: 92px;
  }
  .brand__name {
    font-family: "Montserrat", sans-serif; font-weight: 800;
    font-size: 74px; line-height: 1; color: var(--orange); letter-spacing: 2px;
  }
  .brand__tagline {
    font-family: "Montserrat", sans-serif; font-weight: 800;
    font-size: 9.5px; color: var(--orange); letter-spacing: .6px; margin-top: 6px;
  }
  .ghost-name {
    position: absolute; right: -6px; bottom: -26px;
    font-family: "Montserrat", sans-serif; font-weight: 800;
    font-size: 128px; color: var(--ghost); letter-spacing: 2px; line-height: 1;
  }
  .contacts {
    position: absolute; left: 40px; bottom: 24px; list-style: none;
  }
  .contacts li {
    display: flex; align-items: center; gap: 9px;
    color: var(--white); font-size: 13.5px; line-height: 21px;
  }
  .contacts svg { width: 13px; height: 13px; flex: none; }
</style>
</head>
<body>
  <section class="card card--back" aria-label="Card back">
    <div class="back-pattern" role="img" aria-label="Dark repeating wordmark pattern fading across the card"></div>
    <div class="back-mark">Velk</div>
  </section>

  <section class="card card--front" aria-label="Card front">
    <div class="accent-bar"></div>
    <div class="ghost-name" aria-hidden="true">VELK</div>

    <div class="person">
      <div class="person__name"><span class="person__first">Mira</span> <span class="person__last">Holanek</span></div>
      <div class="person__role">Sales; Installer</div>
    </div>

    <div class="brand">
      <div class="brand__name">Velk</div>
      <div class="brand__tagline">AUTOMATION AND SECURITY SERVICES</div>
    </div>

    <ul class="contacts">
      <li>
        <svg viewBox="0 0 16 16"><path fill="#f28b45" d="M3.5 1.5l2.5 3-1.5 1.8c.9 2 2.3 3.4 4.2 4.2l1.8-1.5 3 2.5-1.6 2.2C7 13.5 2.5 9 1.3 3.1z"/></svg>
        555.418.7260
      </li>
      <li>
        <svg viewBox="0 0 16 16"><rect x="4" y="1" width="8" height="14" rx="1.5" fill="none" stroke="#f28b45" stroke-width="1.4"/><circle cx="8" cy="12.5" r=".9" fill="#f28b45"/></svg>
        555.418.9031
      </li>
      <li>
        <svg viewBox="0 0 16 16"><circle cx="8" cy="8" r="6.5" fill="none" stroke="#f28b45" stroke-width="1.4"/><ellipse cx="8" cy="8" rx="2.8" ry="6.5" fill="none" stroke="#f28b45" stroke-width="1.2"/><line x1="1.5" y1="8" x2="14.5" y2="8" stroke="#f28b45" stroke-width="1.2"/></svg>
        www.GuardedByVelk.example
      </li>
      <li>
        <svg viewBox="0 0 16 16"><rect x="1.5" y="3.5" width="13" height="9" rx="1" fill="none" stroke="#f28b45" stroke-width="1.4"/><path d="M1.5 4l6.5 5 6.5-5" fill="none" stroke="#f28b45" stroke-width="1.4"/></svg>
        info@GuardedByVelk.example
      </li>
    </ul>
  </section>
</body>
</html>
```